Investment company needing business card

We are wanting a business card which looks sharp and easy on the eye. We are thinking of having a business card with the logo embossed on it, to really make it stand out. We will only have a small amount of information of the business card, person's name, position, email address and phone number

Contact Information for Business Card

Danielle Frost
Executive Assistant
+64 21 473 5162
danielf@harwickpartners.co.nz

Requirements
Must have
• Embossed logo
Should not have
• Not to be busy

```html
<!DOCTYPE html>
<html lang="en">
<head>
<meta charset="utf-8">
<title>Harwick Partners – Business Card</title>
<link href="https://fonts.googleapis.com/css2?family=Roboto:wght@400;500&family=Michroma&display=swap" rel="stylesheet">
<style>
  :root {
    --backdrop: #2b2b2d;
    --card: #1f1f21;
    --card-edge: #29292b;
    --green: #1fb774;
    --white: #f2f2f2;
    --emboss: #3a3a3d;
  }
  * { margin: 0; padding: 0; box-sizing: border-box; }
  html, body { width: 1200px; height: 900px; overflow: hidden; }
  body {
    background: var(--backdrop);
    font-family: "Roboto", Arial, sans-serif;
    position: relative;
  }
  .card {
    position: absolute;
    left: 250px;
    width: 700px;
    height: 400px;
    background: linear-gradient(135deg, var(--card-edge), var(--card));
    box-shadow: 0 10px 30px rgba(0,0,0,0.45);
  }
  .card-front { top: 30px; }
  .card-back { top: 470px; }

  .brand-name {
    font-family: "Michroma", Arial, sans-serif;
    font-weight: 400;
    letter-spacing: 2px;
    white-space: nowrap;
  }
  .card-front .brand {
    position: absolute;
    inset: 0;
    display: flex;
    align-items: center;
    justify-content: center;
  }
  .card-front .brand-name {
    font-size: 38px;
    color: var(--emboss);
    text-shadow: none;
  }

  .card-back .brand {
    position: absolute;
    top: 52px;
    right: 44px;
    display: flex;
    align-items: center;
    gap: 12px;
  }
  .card-back .brand-mark {
    width: 34px; height: 34px;
    background: var(--green);
  }
  .card-back .brand-name {
    font-size: 24px;
    color: var(--green);
  }

  .person {
    position: absolute;
    left: 48px;
    top: 178px;
  }
  .person-name {
    font-size: 36px;
    font-weight: 500;
    color: var(--green);
    letter-spacing: 1px;
    text-transform: uppercase;
    line-height: 1;
  }
  .person-role {
    font-size: 17px;
    color: var(--white);
    margin-top: 4px;
  }
  .divider {
    position: absolute;
    left: 48px;
    right: 44px;
    top: 262px;
    height: 2px;
    background: var(--green);
  }
  .contacts {
    position: absolute;
    left: 48px;
    top: 286px;
    list-style: none;
  }
  .contact {
    display: flex;
    align-items: center;
    gap: 12px;
    font-size: 18px;
    color: var(--white);
    line-height: 26px;
  }
  .contact svg { width: 14px; height: 14px; flex: none; }
</style>
</head>
<body>
  <section class="card card-front">
    <div class="brand">
      <span class="brand-name">HARWICK PARTNERS</span>
    </div>
  </section>

  <section class="card card-back">
    <div class="brand">
      <span class="brand-mark"></span>
      <span class="brand-name">HARWICK PARTNERS</span>
    </div>

    <div class="person">
      <h1 class="person-name">Danielle Frost</h1>
      <p class="person-role">Executive Assistant</p>
    </div>

    <div class="divider"></div>

    <ul class="contacts">
      <li class="contact">
        <svg viewBox="0 0 24 24"><path fill="#1fb774" d="M6.6 10.8a15 15 0 0 0 6.6 6.6l2.2-2.2c.3-.3.7-.4 1-.2 1.1.4 2.3.6 3.6.6.6 0 1 .4 1 1V20c0 .6-.4 1-1 1A17 17 0 0 1 3 4c0-.6.4-1 1-1h3.5c.6 0 1 .4 1 1 0 1.3.2 2.5.6 3.6.1.3 0 .7-.2 1z"/></svg>
        <span>+64 21 473 5162</span>
      </li>
      <li class="contact">
        <svg viewBox="0 0 24 24"><rect x="2" y="5" width="20" height="14" fill="none" stroke="#1fb774" stroke-width="2"/><path d="M2 5l10 8 10-8" fill="none" stroke="#1fb774" stroke-width="2"/></svg>
        <span>danielf@harwickpartners.co.nz</span>
      </li>
      <li class="contact">
        <svg viewBox="0 0 24 24"><circle cx="12" cy="12" r="10" fill="none" stroke="#1fb774" stroke-width="2"/><path d="M2 12h20M12 2c3 3 3 17 0 20M12 2c-3 3-3 17 0 20" fill="none" stroke="#1fb774" stroke-width="1.6"/></svg>
        <span>www.harwickpartners.co.nz</span>
      </li>
    </ul>
  </section>
</body>
</html>
```